Design a product reviews website

We need a website design and simple logo for the brand Venlotix.com. The website will provide reviews of technology products and services. The brand and website should be approachable but should also be trustworthy and high quality. The deliverable should be designs, specs and assets that I can provide to a development team to build the website.

Target Market(s)

People researching products to buy.

Industry/Entity Type

Product

Logo Text

Venlotix.com

Number of Pages Required

5+ page

Font styles to use
Sans Serif

Colors
0492cd
0355a3
3176b5
33a6d7
85cae6
85abd2
cedeed
cee9f5

Requirements
Must have
• - Designs for the Homepage, Category and Article pages.
• - Designs for web and mobile.
• - Designs details for the engineering team to use for development.
• - I'm open to other colors than the preferences I chose but I'm more likely to like blues, greys and blacks.

```html
<!DOCTYPE html>
<html lang="en">
<head>
<meta charset="utf-8">
<title>Venlotix – Product Reviews</title>
<link href="https://fonts.googleapis.com/css2?family=Bitter:ital,wght@0,400;0,600;0,700;1,400&family=Montserrat:wght@600;700;800&display=swap" rel="stylesheet">
<style>
:root{
  --blue-dark:#0355a3;
  --blue:#3176b5;
  --blue-mid:#2e6fb6;
  --sky:#33a6d7;
  --sky-light:#85cae6;
  --ink:#222;
  --text:#444;
  --muted:#666;
  --page:#f4f4f4;
  --line:#dcdcdc;
  --footer:#2a2a2a;
  --footer-deep:#1f1f1f;
  --star:#f39c12;
  --white:#fff;
}
*{box-sizing:border-box;margin:0;padding:0}
html,body{width:1200px;height:2985px;overflow:hidden}
body{position:relative;font-family:"Bitter",Georgia,serif;color:var(--text);background:var(--page)}
.abs{position:absolute}
a{color:inherit}

/* header */
.site-header{left:0;top:0;width:1200px;height:76px;background:var(--white)}
.logo{left:86px;top:22px;font-family:"Montserrat",Arial,sans-serif;font-weight:800;font-size:26px;color:var(--blue-dark);letter-spacing:.5px}
.search{left:846px;top:21px;width:222px;height:36px;border:1px solid #9bb6d2;border-radius:4px;font-size:12px;color:#333;padding:10px 12px}
.search svg{position:absolute;right:10px;top:9px}
.menu-btn{left:1082px;top:20px;width:38px;height:38px;background:var(--blue-dark);border-radius:4px}
.menu-btn i{position:absolute;left:11px;width:16px;height:2px;background:#fff}

/* hero */
.hero{left:0;top:76px;width:1200px;height:614px;background:linear-gradient(135deg,#7e8b95 0%,#5b6873 45%,#3e4a55 100%)}
.hero-band{left:0;top:290px;width:560px;height:172px;background:rgba(30,36,42,.78)}
.hero-kicker{left:86px;top:324px;font-family:"Montserrat",Arial,sans-serif;font-weight:700;font-size:20px;color:#fff}
.hero-title{left:86px;top:356px;font-family:"Montserrat",Arial,sans-serif;font-weight:700;font-size:30px;line-height:38px;color:#fff}
.dot{top:572px;width:26px;height:26px;border:3px solid #fff;border-radius:50%}
.dot.on{background:var(--sky)}

/* sidebar */
.side-nav{left:72px;top:730px;width:264px;background:var(--blue);list-style:none}
.side-nav li{height:54px;border-bottom:1px solid rgba(255,255,255,.18);display:flex;align-items:center;padding-left:16px;color:#fff;font-size:15px;position:relative}
.side-nav li.active{background:var(--blue-dark)}
.side-nav li svg.ic{margin-right:12px;opacity:.75}
.side-nav li::after{content:"";position:absolute;right:16px;top:22px;width:8px;height:8px;border-top:2px solid #fff;border-right:2px solid #fff;transform:rotate(45deg)}

/* section headings */
.col-head{height:50px;background:var(--blue-dark);color:#fff;font-size:16px;font-weight:600;padding:15px 18px;letter-spacing:.3px}

/* cards */
.card{background:#fff;border:1px solid var(--line)}
.photo{position:absolute;left:0;top:0;width:100%}
.stars{position:absolute;left:20px;color:var(--star);font-size:20px;letter-spacing:3px}
.stars span{color:#9a9a9a}
.card h3{position:absolute;left:20px;font-size:19px;font-weight:600;color:var(--ink)}
.card p{position:absolute;left:20px;right:20px;font-size:13px;line-height:22px;color:var(--text)}
.card-bar{position:absolute;left:0;bottom:0;width:100%;height:38px;background:var(--sky);color:#fff;font-size:12px;font-style:italic;display:flex;align-items:center;padding-left:14px;gap:22px}
.card-bar a{text-decoration:underline}
.card-bar .go{position:absolute;right:0;top:0;width:40px;height:38px;background:var(--blue-dark)}
.card-bar .go::after,.arrow-btn::after{content:"";position:absolute;left:14px;top:15px;width:8px;height:8px;border-top:2px solid #fff;border-right:2px solid #fff;transform:rotate(45deg)}
.avatar{width:22px;height:22px;border-radius:50%;background:#e6eef6;border:2px solid #fff;display:inline-block;vertical-align:middle;margin-right:8px}
.meta{display:inline-flex;align-items:center;gap:6px}

.loading{left:362px;top:1964px;width:486px;height:38px;border:1px solid #bdbdbd;border-radius:4px;background:#fff;font-size:13px;font-style:italic;text-align:center;padding-top:10px;color:#333}

.pop h4{position:absolute;left:18px;font-size:18px;font-weight:400;color:var(--ink)}
.pop .tags{position:absolute;left:18px;font-size:12px;font-style:italic;color:#444}
.pop .tags a{text-decoration:underline}
.arrow-btn{position:absolute;right:18px;width:38px;height:38px;background:var(--blue-mid)}
.pop .stars{left:18px;background:rgba(40,40,40,.8);padding:2px 8px;font-size:19px;border-radius:2px}

/* about */
.about{left:0;top:2048px;width:1200px;height:442px;background:linear-gradient(180deg,#3a7dbe,#2f72b3)}
.about-img{left:60px;top:2100px;width:1080px;height:380px;background:radial-gradient(ellipse at center,rgba(255,255,255,.10),rgba(255,255,255,0) 70%)}
.about h2{position:absolute;left:0;top:108px;width:1200px;text-align:center;font-size:38px;font-weight:400;color:#fff;letter-spacing:1px}
.about .rule{position:absolute;left:540px;top:170px;width:120px;height:1px;background:rgba(255,255,255,.6)}
.about p{position:absolute;left:210px;top:194px;width:780px;text-align:center;color:#fff;font-size:14px;font-weight:600;line-height:28px}

/* footer */
.footer{left:0;top:2490px;width:1200px;height:450px;background:var(--footer)}
.newsletter{left:84px;top:2542px;width:720px;height:70px;border:1px solid #8a8a8a;border-radius:4px}
.newsletter .lbl{position:absolute;left:54px;top:22px;color:#fff;font-size:19px}
.newsletter .field{position:absolute;left:240px;top:16px;width:360px;height:38px;background:#fff;font-size:13px;color:#333;padding:11px 12px}
.newsletter .btn{position:absolute;left:600px;top:16px;width:104px;height:38px;background:var(--sky);color:#fff;font-size:13px;font-weight:700;text-align:center;padding-top:11px;letter-spacing:.5px}
.follow{left:842px;top:2562px;color:#fff;font-size:19px;font-weight:600}
.social{top:2560px;width:32px;height:32px;border:2px solid #fff;border-radius:50%;background:var(--blue-dark)}
.f-title{color:#fff;font-size:22px}
.f-rule{height:1px;background:#555}
.field-box{border:1px solid #aaa;color:#fff;font-size:13px;padding:10px 12px}
.submit{background:var(--sky);color:#fff;font-weight:700;font-size:14px;text-align:center;padding-top:11px;letter-spacing:1px}
.vline{width:1px;background:#444}
.links{list-style:none;color:#fff;font-size:14px}
.links li{height:27px}
.links li::before{content:"›";margin-right:10px}
.links li.cur{font-weight:700}
.contact{color:#fff;font-size:13px;line-height:22px}
.bottom-bar{left:0;top:2940px;width:1200px;height:45px;background:var(--footer-deep);border-top:8px solid var(--blue-dark);color:#fff;font-size:13px;text-align:center;padding-top:12px}
.to-top{left:584px;top:2926px;width:32px;height:16px;background:var(--blue-dark);border-radius:16px 16px 0 0}
</style>
</head>
<body>

<header class="site-header abs">
  <div class="logo abs">VENLOTIX</div>
  <div class="search abs">Search Here
    <svg width="16" height="16" viewBox="0 0 16 16"><circle cx="6.5" cy="6.5" r="5" fill="none" stroke="#3176b5" stroke-width="1.6"/><path d="M10 10l4.5 4.5" stroke="#3176b5" stroke-width="1.6"/></svg>
  </div>
  <div class="menu-btn abs"><i style="top:12px"></i><i style="top:18px"></i><i style="top:24px"></i></div>
</header>

<section class="hero abs" role="img" aria-label="Photo of a security camera mounted on a grey concrete wall"></section>
<div class="hero-band abs"></div>
<div class="hero-kicker abs">KNOW BEST DEAL ON</div>
<div class="hero-title abs">HOME APPLIANCES &amp;<br>ELECTRONIC GADGETS</div>
<div class="dot on abs" style="left:544px"></div>
<div class="dot abs" style="left:588px"></div>
<div class="dot abs" style="left:632px"></div>

<ul class="side-nav abs">
  <li class="active"><svg class="ic" width="16" height="14" viewBox="0 0 16 14"><path d="M8 1L1 7h2v6h4V9h2v4h4V7h2z" fill="#fff"/></svg>Home</li>
  <li><svg class="ic" width="16" height="14" viewBox="0 0 16 14"><rect x="1" y="4" width="14" height="8" fill="#fff"/></svg>Appliances</li>
  <li><svg class="ic" width="16" height="14" viewBox="0 0 16 14"><rect x="1" y="1" width="14" height="9" fill="none" stroke="#fff" stroke-width="1.6"/><path d="M5 13h6" stroke="#fff" stroke-width="1.6"/></svg>Computers</li>
  <li><svg class="ic" width="16" height="14" viewBox="0 0 16 14"><circle cx="8" cy="7" r="6" fill="none" stroke="#fff" stroke-width="1.6"/><circle cx="8" cy="7" r="2" fill="#fff"/></svg>Electronics</li>
  <li><svg class="ic" width="16" height="14" viewBox="0 0 16 14"><path d="M1 4h10l4 3-4 2H1z" fill="#fff"/></svg>Home Security</li>
  <li><svg class="ic" width="16" height="14" viewBox="0 0 16 14"><rect x="5" y="0" width="7" height="14" rx="1" fill="none" stroke="#fff" stroke-width="1.6"/></svg>Mobile</li>
  <li><svg class="ic" width="16" height="14" viewBox="0 0 16 14"><rect x="1" y="2" width="10" height="10" fill="#fff"/><path d="M12 5h3v7h-3" fill="#fff"/></svg>Smart Home</li>
  <li><svg class="ic" width="16" height="14" viewBox="0 0 16 14"><circle cx="8" cy="7" r="6" fill="none" stroke="#fff" stroke-width="1.6"/><path d="M5 7l2 2 4-4" stroke="#fff" stroke-width="1.6" fill="none"/></svg>Software</li>
</ul>

<!-- latest products -->
<div class="col-head abs" style="left:362px;top:730px;width:486px">LATEST PRODUCTS</div>

<article class="card abs" style="left:362px;top:792px;width:486px;height:370px">
  <div class="photo" role="img" aria-label="Photo of a speaker set with subwoofer" style="height:176px;background:linear-gradient(180deg,#f4f4f4,#dcdcdc)"></div>
  <div class="stars" style="top:188px">★★★★<span>★</span></div>
  <h3 style="top:226px">The Smart Speaker</h3>
  <p style="top:258px">Lorem ipsum dolor sit amet, consectetuer adipiscing elit, sed diam nonummy nibh euismod tincidunt ut laoreet dolore magna</p>
  <div class="card-bar"><span class="meta"><i class="avatar"></i>By John</span><span class="meta">▦ On 11/08/2016</span><span class="meta">✎ In <a>Home</a>, <a>Speakers</a></span><div class="go"></div></div>
</article>

<article class="card abs" style="left:362px;top:1186px;width:234px;height:362px">
  <div class="photo" role="img" aria-label="Photo of a built-in kitchen oven" style="height:176px;background:linear-gradient(180deg,#9a9a9a,#3a3a3a)"></div>
  <div class="stars" style="top:188px">★★★★<span>★</span></div>
  <h3 style="top:222px">Kitchen Appliances</h3>
  <p style="top:250px">Lorem ipsum dolor sit amet, consectetuer adipiscing elit</p>
  <div class="card-bar"><span class="meta">✎ In <a>Home</a>, <a>Kitchen</a></span><div class="go"></div></div>
</article>

<article class="card abs" style="left:616px;top:1186px;width:232px;height:362px">
  <div class="photo" role="img" aria-label="Photo of a juicer mixer grinder" style="height:176px;background:linear-gradient(180deg,#5a4638,#a07c5c)"></div>
  <div class="stars" style="top:188px">★★★★<span>★</span></div>
  <h3 style="top:222px">Juicer Mixer Grinder</h3>
  <p style="top:250px">Lorem ipsum dolor sit amet, consectetuer adipiscing elit</p>
  <div class="card-bar"><span class="meta">✎ In <a>Home</a>, <a>Kitchen</a></span><div class="go"></div></div>
</article>

<article class="card abs" style="left:362px;top:1570px;width:486px;height:372px">
  <div class="photo" role="img" aria-label="Photo of a home theater with television and speakers" style="height:176px;background:linear-gradient(180deg,#d8d3c8,#3a3530)"></div>
  <div class="stars" style="top:190px">★★★★<span>★</span></div>
  <h3 style="top:228px">Home Theater</h3>
  <p style="top:258px">Lorem ipsum dolor sit amet, consectetuer adipiscing elit, sed diam nonummy nibh euismod tincidunt ut laoreet dolore magna</p>
  <div class="card-bar"><span class="meta"><i class="avatar"></i>By John</span><span class="meta">▦ On 11/08/2016</span><span class="meta">✎ In <a>Home</a>, <a>Electronics</a></span><div class="go"></div></div>
</article>

<div class="loading abs">◌ &nbsp;Loading</div>

<!-- popular products -->
<div class="col-head abs" style="left:876px;top:730px;width:256px">POPULAR PRODUCTS</div>

<article class="card pop abs" style="left:876px;top:792px;width:256px;height:254px">
  <div class="photo" role="img" aria-label="Photo of hanging copper pots" style="height:176px;background:linear-gradient(180deg,#b09a84,#7a4a2e)"></div>
  <div class="stars" style="top:128px">★★★★<span>★</span></div>
  <h4 style="top:190px">Copper Pots</h4>
  <div class="tags" style="top:220px">✎ In <a>Home</a>, <a>Utensils</a></div>
  <div class="arrow-btn" style="top:196px"></div>
</article>

<article class="card pop abs" style="left:876px;top:1070px;width:256px;height:256px">
  <div class="photo" role="img" aria-label="Photo of wireless speakers" style="height:176px;background:linear-gradient(180deg,#2a2a2a,#0e0e0e)"></div>
  <div class="stars" style="top:128px">★★★★<span>★</span></div>
  <h4 style="top:190px">Wireless Speakers</h4>
  <div class="tags" style="top:220px">✎ In <a>Home</a>, <a>Speakers</a></div>
  <div class="arrow-btn" style="top:196px"></div>
</article>

<article class="card pop abs" style="left:876px;top:1350px;width:256px;height:256px">
  <div class="photo" role="img" aria-label="Photo of an electrical iron" style="height:176px;background:linear-gradient(180deg,#f2f2f2,#d4dde4)"></div>
  <div class="stars" style="top:128px">★★★★<span>★</span></div>
  <h4 style="top:190px">Electrical Iron</h4>
  <div class="tags" style="top:220px">✎ In <a>Home</a>, <a>Utensils</a></div>
  <div class="arrow-btn" style="top:196px"></div>
</article>

<article class="card pop abs" style="left:876px;top:1630px;width:256px;height:256px">
  <div class="photo" role="img" aria-label="Photo of hanging copper pots" style="height:176px;background:linear-gradient(180deg,#b09a84,#7a4a2e)"></div>
  <div class="stars" style="top:128px">★★★★<span>★</span></div>
  <h4 style="top:190px">Copper Pots</h4>
  <div class="tags" style="top:220px">✎ In <a>Home</a>, <a>Utensils</a></div>
  <div class="arrow-btn" style="top:196px"></div>
</article>

<!-- about -->
<section class="about abs">
  <h2>ABOUT VENLOTIX</h2>
  <div class="rule"></div>
  <p>Lorem ipsum dolor sit amet, consectetuer adipiscing elit, sed diam nonummy nibh euismod tincidunt ut laoreet dolore magna aliquam erat volutpat. Ut wisi enim ad minim veniam, quis nostrud exerci tation ullamcorper suscipit lobortis nisl ut aliquip ex ea commodo consequat. Duis autem vel eum iriure dolor in hendrerit in vulputate velit esse molestie consequat, vel illum dolore eu feugiat nulla facilisis at vero eros et accumsan et iusto odio dignissim qui blandit praesent luptatum zzril delenit augue duis dolore te feugait nulla facilisi.</p>
</section>
<div class="about-img abs" role="img" aria-label="Faint photo collage of home electronics"></div>

<!-- footer -->
<footer class="footer abs"></footer>
<div class="newsletter abs">
  <svg class="abs" style="left:16px;top:20px" width="28" height="28" viewBox="0 0 28 28"><path d="M3 11l11-8 11 8v14H3z" fill="none" stroke="#85cae6" stroke-width="2"/><path d="M3 11l11 8 11-8" fill="none" stroke="#85cae6" stroke-width="2"/></svg>
  <div class="lbl">Newsletter Signup</div>
  <div class="field">Enter your email here</div>
  <div class="btn">SUBSCRIBE</div>
</div>
<div class="follow abs">Follow Us</div>
<div class="social abs" style="left:948px"></div>
<div class="social abs" style="left:990px"></div>
<div class="social abs" style="left:1032px"></div>
<div class="social abs" style="left:1074px"></div>

<svg class="abs" style="left:84px;top:2656px" width="26" height="26" viewBox="0 0 26 26"><circle cx="13" cy="13" r="11" fill="none" stroke="#85cae6" stroke-width="2"/><text x="13" y="18" text-anchor="middle" font-size="14" fill="#85cae6" font-family="Bitter,serif">?</text></svg>
<div class="f-title abs" style="left:122px;top:2654px">Quick Inquiry</div>
<div class="f-rule abs" style="left:84px;top:2692px;width:470px"></div>
<div class="field-box abs" style="left:84px;top:2724px;width:226px;height:38px">Name</div>
<div class="field-box abs" style="left:84px;top:2780px;width:226px;height:38px">Email Address</div>
<div class="field-box abs" style="left:84px;top:2838px;width:226px;height:38px">Phone Number</div>
<div class="field-box abs" style="left:328px;top:2724px;width:228px;height:94px">Message</div>
<div class="submit abs" style="left:328px;top:2838px;width:228px;height:38px">SUBMIT</div>

<div class="vline abs" style="left:596px;top:2650px;height:256px"></div>
<div class="vline abs" style="left:834px;top:2650px;height:256px"></div>

<svg class="abs" style="left:628px;top:2658px" width="20" height="24" viewBox="0 0 20 24"><rect x="2" y="3" width="16" height="19" fill="none" stroke="#85cae6" stroke-width="2"/><path d="M6 10h8M6 14h8M6 18h6" stroke="#85cae6" stroke-width="1.6"/></svg>
<div class="f-title abs" style="left:660px;top:2656px">Quick Links</div>
<div class="f-rule abs" style="left:628px;top:2694px;width:180px"></div>
<ul class="links abs" style="left:630px;top:2710px">
  <li class="cur">Home</li><li>About Us</li><li>Our Products</li><li>Support</li><li>Faqs</li><li>Contact Us</li>
</ul>

<svg class="abs" style="left:868px;top:2656px" width="24" height="24" viewBox="0 0 24 24"><circle cx="12" cy="12" r="10" fill="none" stroke="#85cae6" stroke-width="2"/><path d="M2 12h20M12 2c4 4 4 16 0 20M12 2c-4 4-4 16 0 20" fill="none" stroke="#85cae6" stroke-width="1.4"/></svg>
<div class="f-title abs" style="left:906px;top:2654px">Contact Information</div>
<div class="f-rule abs" style="left:868px;top:2692px;width:264px"></div>
<svg class="abs" style="left:870px;top:2714px" width="14" height="18" viewBox="0 0 14 18"><path d="M7 1a6 6 0 016 6c0 4-6 10-6 10S1 11 1 7a6 6 0 016-6z" fill="#fff"/><circle cx="7" cy="7" r="2" fill="#2a2a2a"/></svg>
<div class="contact abs" style="left:898px;top:2712px">VENLOTIX,<br>Lorem ipsum dolor sit amet,<br>consec tetuer adipiscing elit, sed</div>
<svg class="abs" style="left:870px;top:2790px" width="16" height="16" viewBox="0 0 16 16"><path d="M3 1l3 3-2 2c1 2 3 4 5 5l2-2 3 3-2 3C7 15 1 9 0 4z" fill="#fff"/></svg>
<div class="contact abs" style="left:898px;top:2788px;font-weight:700">123-456-7890</div>
<svg class="abs" style="left:870px;top:2846px" width="16" height="12" viewBox="0 0 16 12"><rect x="0" y="0" width="16" height="12" fill="#fff"/><path d="M0 0l8 6 8-6" fill="none" stroke="#2a2a2a" stroke-width="1.4"/></svg>
<div class="contact abs" style="left:898px;top:2842px">info@venlotix.com</div>

<div class="to-top abs"></div>
<div class="bottom-bar abs">Copyright 2016 <b>VENLOTIX</b> | All Right Reserved.</div>

</body>
</html>
```